Website for software company "velora"

We need a website for our software company/startup named "velora". We are developing several products (currently 3 standard-software products) which are all in different sectors, but all our products are available for Laptops/PC/Mobile Phones/Tablets, ... We do also create custom software and support our customers with consulting to optimize their processes.
We already have a Logo which you can find in the attached files.
We are a young team of 4 members (two founders and 2 employees).

To get an idea of our products -> the first one is a planning software for healthcare organizations (eg. BlueHaven, firebrigade, pharmacy), the second one is a booking software for sport clubs and the third one is a competition software for sports hunting. You see very diverse. Include or ignore this info of our products as you like.

The design has to be a bootstrap 4 (or higher) design. We have licenced FontAwesome as iconset. Responsive design should come without saying.

• Starting page, product pages, news section, contact, team, services

```html
<!DOCTYPE html>
<html lang="en">
<head>
<meta charset="utf-8">
<title>Velora — Software &amp; Consulting</title>
<link href="https://fonts.googleapis.com/css2?family=Montserrat:wght@300;400;500;600;700;800&display=swap" rel="stylesheet">
<style>
:root{
  --orange:#f47f2a;
  --dark:#28313c;
  --ink:#1d2129;
  --text:#3a3f47;
  --muted:#6d727a;
  --light:#eef0f4;
  --white:#ffffff;
  --line:#d9dce2;
}
*{margin:0;padding:0;box-sizing:border-box}
html,body{width:1200px;height:4515px;overflow:hidden}
body{font-family:'Montserrat',sans-serif;color:var(--text);background:var(--white);position:relative}
.abs{position:absolute}
.btn{position:absolute;display:flex;align-items:center;justify-content:center;border-radius:24px;font-weight:700;font-size:13px;letter-spacing:.3px;text-transform:uppercase;text-decoration:none}
.btn-orange{background:var(--orange);color:var(--white)}
.btn-dark{background:var(--dark);color:var(--white)}
.btn-outline-light{border:2px solid var(--white);color:var(--white)}
.btn-outline-orange{border:1.5px solid var(--orange);color:var(--orange);font-size:9px}
.brand{font-weight:700;letter-spacing:2px;display:flex;align-items:center;gap:10px;text-transform:uppercase}
.brand-dot{width:14px;height:14px;background:var(--orange)}

.hero{left:0;top:0;width:1200px;height:713px;background:linear-gradient(100deg,#2f3945 0%,#27303b 45%,#1e252e 100%);overflow:hidden}
.hero-visual{left:520px;top:82px;width:680px;height:631px;background:radial-gradient(ellipse at 45% 35%,rgba(150,165,185,.38) 0%,rgba(60,72,88,.25) 40%,rgba(30,37,46,0) 75%)}
.nav{left:0;top:0;width:1200px;height:82px;border-bottom:1px solid rgba(255,255,255,.12)}
.nav .brand{position:absolute;left:126px;top:22px;color:var(--white);font-size:36px}
.nav-links{position:absolute;left:420px;top:26px;display:flex;height:35px;align-items:center}
.nav-links a{color:var(--white);font-size:12px;font-weight:600;text-decoration:none;text-transform:uppercase}
.nav-links a.active{color:var(--orange)}
.hero-title{left:109px;top:255px;color:var(--white);font-size:37px;line-height:41px;text-transform:uppercase}
.hero-title .light{font-weight:300}
.hero-title .bold{font-weight:700}
.hero-text{left:112px;top:390px;width:410px;color:#e3e6ea;font-size:15px;line-height:21px}
.arrow{top:318px}

.about{left:0;top:713px;width:1200px;height:639px;background:var(--white)}
.about-frame{left:114px;top:114px;width:441px;height:347px;border:5px solid var(--orange)}
.about-photo{left:133px;top:133px;width:470px;height:366px;background:linear-gradient(120deg,#3a4656 0%,#6b6250 45%,#b9823e 70%,#2b3542 100%)}
.about-card{left:557px;top:170px;width:529px;height:366px;background:var(--white);box-shadow:0 6px 28px rgba(0,0,0,.1)}
.about-card h2{position:absolute;left:60px;top:48px;font-size:32px;font-weight:400;color:var(--ink);letter-spacing:.5px;text-transform:uppercase}
.about-card h2 b{font-weight:700}
.about-card p{position:absolute;left:60px;width:430px;font-size:12.5px;line-height:19px;color:var(--text)}
.dots{background-image:radial-gradient(#9aa0a8 1.2px,transparent 1.3px);background-size:9px 9px}

.software{left:0;top:1352px;width:1200px;height:1180px;background:var(--light)}
.section-title{font-size:34px;font-weight:400;color:var(--ink);text-transform:uppercase;letter-spacing:.5px}
.section-title b{font-weight:700}
.underline{height:3px;width:56px;background:var(--orange)}
.planning h3{position:absolute;left:187px;top:211px;font-size:24px;font-weight:700;color:var(--ink);text-transform:uppercase}
.planning p{position:absolute;left:187px;width:440px;font-size:13.5px;line-height:26px;color:var(--text)}
.screenshot{border-radius:10px;background:linear-gradient(160deg,#f6f8fc 0%,#dfe7f3 55%,#c3c8d0 100%)}
.card{top:675px;width:473px;height:406px}
.card-booking{left:121px;background:var(--orange)}
.card-competition{left:631px;background:var(--white)}
.card h4{position:absolute;left:0;width:100%;top:232px;text-align:center;font-size:20px;font-weight:700;text-transform:uppercase}
.card p{position:absolute;left:0;width:100%;top:268px;text-align:center;font-size:13px;line-height:20px;padding:0 40px}

.services{left:0;top:2532px;width:1200px;height:600px;background:linear-gradient(90deg,#222b35 0%,#26303b 38%,#2a3340 100%);overflow:hidden}
.services-photo{left:420px;top:0;width:780px;height:600px;background:radial-gradient(ellipse at 70% 35%,#6b5a4e 0%,#3d4654 35%,rgba(36,45,56,0) 75%),radial-gradient(ellipse at 40% 70%,rgba(90,150,185,.35) 0%,rgba(36,45,56,0) 55%)}
.services p{position:absolute;left:126px;width:440px;color:#e6e9ee;font-size:15px;line-height:26px}

.news{left:0;top:3132px;width:1200px;height:547px;background:var(--white)}
.news-card{top:140px;width:295px}
.news-img{width:295px;height:197px}
.news-date{position:absolute;left:31px;top:200px;font-size:10px;font-weight:700;color:var(--ink)}
.news-title{position:absolute;left:31px;top:220px;width:260px;font-size:13px;line-height:19px;font-weight:700;color:var(--ink)}
.news-text{position:absolute;left:31px;top:264px;width:245px;font-size:10.5px;line-height:19px;color:var(--muted)}

.contact{left:0;top:3679px;width:1200px;height:487px;overflow:hidden;background:var(--orange)}
.contact-photo{left:0;top:0;width:1200px;height:487px}
.contact-heading{left:130px;top:150px;color:var(--white);font-size:26px;line-height:30px;text-transform:uppercase}
.contact-heading b{font-weight:700}
.contact-heading span{font-weight:300;display:block}
.contact-text{left:130px;top:264px;width:340px;color:var(--white);font-size:14.5px;line-height:23px}

.footer{left:0;top:4166px;width:1200px;height:349px;background:var(--white)}
.footer .brand{position:absolute;left:140px;top:70px;font-size:36px;color:var(--ink)}
.footer-about{left:138px;top:133px;width:240px;font-size:10.5px;line-height:16px;color:var(--muted)}
.footer-divider{top:12px;width:1px;height:202px;background:var(--line)}
.footer-col h5{font-size:12px;font-weight:700;color:var(--ink);text-transform:uppercase;display:flex;align-items:center;gap:10px}
.footer-col h5::before{content:"";border-left:6px solid var(--ink);border-top:6px solid transparent;border-bottom:6px solid transparent}
.footer-col ul{list-style:none;margin:13px 0 0 19px}
.footer-col li{font-size:12px;line-height:28px;color:var(--text)}
.social{display:flex;gap:7px;margin:19px 0 0 18px}
.social span{width:28px;height:28px;border-radius:50%;background:var(--ink)}
.social span:first-child{background:var(--orange)}
.copyright-line{left:0;top:293px;width:1200px;height:1px;background:var(--line)}
.copyright{left:0;top:317px;width:1200px;text-align:center;font-size:10px;color:var(--muted)}
</style>
</head>
<body>

<section class="abs hero">
  <div class="abs hero-visual" role="img" aria-label="Illustration of a glowing laptop linked to a network of service icons"></div>

  <nav class="abs nav">
    <div class="brand"><span class="brand-dot"></span>velora</div>
    <div class="nav-links">
      <a class="active" href="#">Product</a>
      <a href="#" style="margin-left:63px">Services</a>
      <a href="#" style="margin-left:54px">News</a>
      <a href="#" style="margin-left:56px">Team</a>
      <a href="#" style="margin-left:61px">About</a>
    </div>
    <a class="btn btn-orange" href="#" style="left:960px;top:26px;width:123px;height:35px;font-size:12px">Contact</a>
  </nav>

  <h1 class="abs hero-title"><span class="light">We help customer</span><br><span class="bold">to optimize their<br>processes</span></h1>
  <p class="abs hero-text">Lorem ipsum dolor sit amet, consectetur adipiscing elit, sed do eiusmod tempor incididunt.</p>
  <a class="btn btn-orange" href="#" style="left:109px;top:466px;width:166px;height:46px">Learn more</a>

  <svg class="abs arrow" style="left:36px" width="30" height="60" viewBox="0 0 30 60" aria-hidden="true"><path d="M26 2 L4 30 L26 58" fill="none" stroke="rgba(255,255,255,.8)" stroke-width="2"/></svg>
  <svg class="abs arrow" style="left:1143px" width="30" height="60" viewBox="0 0 30 60" aria-hidden="true"><path d="M4 2 L26 30 L4 58" fill="none" stroke="rgba(255,255,255,.8)" stroke-width="2"/></svg>
</section>

<section class="abs about">
  <div class="abs about-frame"></div>
  <div class="abs about-photo" role="img" aria-label="Two colleagues reviewing data on a monitor in a dim office"></div>
  <div class="abs dots" style="left:883px;top:352px;width:230px;height:200px;opacity:.6"></div>
  <div class="abs about-card">
    <h2>About <b>velora</b></h2>
    <p style="top:114px">Lorem ipsum dolor sit amet, consectetur adipiscing elit, sed do eiusmod tempor incididunt ut labore et dolore magna aliqua.</p>
    <p style="top:171px">Ut enim ad minim veniam, quis nostrud exercitation ullamco laboris nisi ut aliquip ex ea commodo consequat. Duis aute irure dolor in reprehenderit in voluptate velit esse cillum dolore eu fugiat nulla pariatur. Excepteur sint occaecat cupidatat non proident</p>
    <a class="btn btn-orange" href="#" style="left:54px;top:273px;width:151px;height:39px;font-size:12px">Learn more</a>
  </div>
</section>

<section class="abs software">
  <h2 class="abs section-title" style="left:0;width:1200px;text-align:center;top:66px">Our <b>software</b></h2>
  <div class="abs underline" style="left:572px;top:110px"></div>

  <div class="planning">
    <h3>Planning software</h3>
    <p style="top:255px">Lorem ipsum dolor sit amet, consectetur adipiscing elit, sed do eiusmod tempor incididunt ut labore et dolore magna aliqua. Ut enim ad minim veniam, quis nostrud</p>
    <p style="top:347px">exercitation ullamco laboris nisi ut aliquip ex ea commodo consequat. Duis aute irure dolo</p>
    <a class="btn btn-orange" href="#" style="left:186px;top:421px;width:166px;height:44px">Learn more</a>
  </div>

  <div class="abs screenshot" style="left:613px;top:177px;width:498px;height:282px" role="img" aria-label="Planning software dashboard shown on a laptop"></div>

  <div class="abs dots" style="left:440px;top:550px;width:120px;height:60px;opacity:.55"></div>
  <div class="abs dots" style="left:925px;top:550px;width:120px;height:60px;opacity:.55"></div>

  <div class="abs card card-booking">
    <h4 style="color:var(--white)">Booking software</h4>
    <p style="color:#fff3ea">Lorem ipsum dolor sit amet, consectetur adipiscing elit, sed do eiusmod tempor incididunt ut labore</p>
    <a class="btn btn-dark" href="#" style="left:152px;top:320px;width:158px;height:41px">Learn more</a>
  </div>
  <div class="abs screenshot" style="left:175px;top:570px;width:380px;height:290px" role="img" aria-label="Booking app shown on a tablet and phone"></div>

  <div class="abs card card-competition">
    <h4 style="color:var(--ink)">Compeition software</h4>
    <p style="color:var(--muted)">Lorem ipsum dolor sit amet, consectetur adipiscing elit, sed do eiusmod tempor incididunt ut labore</p>
    <a class="btn btn-orange" href="#" style="left:163px;top:320px;width:158px;height:41px">Learn more</a>
  </div>
  <div class="abs screenshot" style="left:657px;top:570px;width:420px;height:248px" role="img" aria-label="Competition software dashboard shown on a laptop"></div>
</section>

<section class="abs services">
  <div class="abs services-photo" role="img" aria-label="Woman in glasses working at a computer with a glowing world map overlay"></div>
  <h2 class="abs section-title" style="left:126px;top:142px;color:var(--white)">Our <b>services</b></h2>
  <div class="abs underline" style="left:126px;top:192px"></div>
  <p style="top:216px">Lorem ipsum dolor sit amet, consectetur adipiscing elit, sed do eiusmod tempor incididunt ut labore</p>
  <p style="top:294px">Ut enim ad minim veniam, quis nostrud exercitation ullamco laboris nisi ut aliquip ex ea commodo consequat. Duis aute irure dolor in reprehenderit in voluptate</p>
  <a class="btn btn-outline-light" href="#" style="left:123px;top:394px;width:178px;height:47px">Learn more</a>
</section>

<section class="abs news">
  <h2 class="abs section-title" style="left:128px;top:70px">Latest <b>news</b></h2>
  <div class="abs underline" style="left:128px;top:114px"></div>

  <article class="abs news-card" style="left:130px">
    <div class="news-img" role="img" aria-label="Hands typing on a laptop next to a monitor showing code" style="background:linear-gradient(135deg,#dfe3e8 0%,#8b939d 50%,#2d3540 100%)"></div>
    <div class="news-date">JAN 24, 2022</div>
    <div class="news-title">Sed ut perspiciatis unde omnis iste natus error sit voluptatem</div>
    <div class="news-text">Lorem ipsum dolor sit amet consectetur adipiscing elit, sed do eiusmod tempor</div>
    <a class="btn btn-outline-orange" href="#" style="left:31px;top:318px;width:110px;height:26px">Learn more</a>
  </article>

  <article class="abs news-card" style="left:448px">
    <div class="news-img" role="img" aria-label="Person pointing at charts on a computer screen in a bright office" style="background:linear-gradient(135deg,#eef1f4 0%,#c9cfd6 50%,#7d8691 100%)"></div>
    <div class="news-date">JAN 24, 2022</div>
    <div class="news-title">Sed ut perspiciatis unde omnis iste natus error sit voluptatem</div>
    <div class="news-text">Lorem ipsum dolor sit amet consectetur adipiscing elit, sed do eiusmod tempor</div>
    <a class="btn btn-outline-orange" href="#" style="left:31px;top:318px;width:110px;height:26px">Learn more</a>
  </article>

  <article class="abs news-card" style="left:766px">
    <div class="news-img" role="img" aria-label="Two colleagues reviewing data on a monitor" style="background:linear-gradient(120deg,#3a4656 0%,#6b6250 45%,#b9823e 70%,#2b3542 100%)"></div>
    <div class="news-date">JAN 24, 2022</div>
    <div class="news-title">Sed ut perspiciatis unde omnis iste natus error sit voluptatem</div>
    <div class="news-text">Lorem ipsum dolor sit amet consectetur adipiscing elit, sed do eiusmod tempor</div>
    <a class="btn btn-outline-orange" href="#" style="left:31px;top:318px;width:110px;height:26px">Learn more</a>
  </article>
</section>

<section class="abs contact">
  <svg class="abs contact-photo" width="1200" height="487" viewBox="0 0 1200 487" role="img" aria-label="Developers collaborating at desks with monitors in an office">
    <defs>
      <linearGradient id="officeTone" x1="0" y1="0" x2="1" y2="1">
        <stop offset="0" stop-color="#8a7a66"/>
        <stop offset=".5" stop-color="#4c5561"/>
        <stop offset="1" stop-color="#2a313a"/>
      </linearGradient>
    </defs>
    <polygon points="666,0 1200,0 1200,487 490,487" fill="url(#officeTone)"/>
  </svg>
  <div class="abs brand" style="left:130px;top:110px;font-size:26px;color:var(--white)">velora</div>
  <h2 class="abs contact-heading"><b>Contact us</b><span>Do you want to start</span><span>development&nbsp; project.</span></h2>
  <p class="abs contact-text">Lorem ipsum dolor sit amet, consectetur adipiscing elit, sed do eiusmod temp+</p>
  <a class="btn btn-dark" href="#" style="left:131px;top:324px;width:167px;height:44px">Contact us</a>
</section>

<footer class="abs footer">
  <div class="brand"><span class="brand-dot"></span>velora</div>
  <p class="abs footer-about">Lorem ipsum dolor sit amet, consectetur adipiscing elit, sed do eiusmod tempor incididunt ut labore et dolore</p>

  <div class="abs footer-divider" style="left:433px"></div>
  <div class="abs footer-divider" style="left:673px"></div>
  <div class="abs footer-divider" style="left:897px"></div>

  <div class="abs footer-col" style="left:433px;top:77px">
    <h5>Navigation</h5>
    <ul><li>About Us</li><li>Products</li><li>Services</li><li>Contact Us</li></ul>
  </div>
  <div class="abs footer-col" style="left:673px;top:77px">
    <h5>Resources</h5>
    <ul><li>News</li><li>Team</li><li>Privacy Policy</li></ul>
  </div>
  <div class="abs footer-col" style="left:897px;top:77px">
    <h5>Follow us</h5>
    <div class="social" aria-label="Social media links"><span></span><span></span><span></span><span></span></div>
  </div>

  <div class="abs copyright-line"></div>
  <p class="abs copyright">© 2022 Velora &nbsp;| All Rights Reserved</p>
</footer>

</body>
</html>
```